Graphic Design Zephyrmart Book Description

There is a book on Zephyrmart that is my competitor that has a large graphic design as part of the description for the book and I want a similar thing for my book to make it stand out more.

My competitors book is here: https://www.zephyrmart.example/Stellar-Chemistry-Novices-Grasping-Walkthrough/dp/K47RTPW612/

My book is here: https://www.zephyrmart.example/Stellar-Chemistry-Groundwork-Reactions-Bonding/dp/K9HXCVT27S/

You can see the kind of thing I am looking for on the book listing but I have attached an image below.

Thanks

Trevor

```html
<!DOCTYPE html>
<html lang="en">
<head>
<meta charset="utf-8">
<title>Book Description Graphic</title>
<link rel="stylesheet" href="https://fonts.googleapis.com/css2?family=Bebas+Neue&family=Montserrat:wght@400;500;700;800&family=Oswald:wght@500;600&display=swap">
<style>
  :root {
    --navy: #070a33;
    --navy-deep: #03051f;
    --yellow: #f2ea2a;
    --white: #ffffff;
    --ink: #111111;
    --col-blue: #e4e8fb;
    --col-yellow: #fcfad6;
    --gold: #d9b33a;
    --gold-dark: #8a6414;
    --bronze: #c98a35;
  }
  * { box-sizing: border-box; margin: 0; padding: 0; }
  html, body { width: 773px; height: 1200px; overflow: hidden; background: var(--white); }
  body { font-family: "Montserrat", sans-serif; }
  .poster { position: relative; width: 773px; height: 1200px; overflow: hidden; background: var(--white); }

  .top-band { position: absolute; left: 0; top: 0; width: 773px; height: 39px; background: var(--navy); }
  .hero-backdrop {
    position: absolute; left: 0; top: 39px; width: 773px; height: 348px;
    background: radial-gradient(ellipse at 45% 95%, #2f6fb4 0%, #173f86 30%, #0b1a4a 60%, var(--navy-deep) 100%);
  }

  .headline { position: absolute; left: 44px; top: 40px; font-family: "Bebas Neue", sans-serif; font-weight: 400; line-height: 67px; font-size: 79px; letter-spacing: 0.3px; }
  .headline .accent { color: var(--yellow); display: block; }
  .headline .main { color: var(--white); display: block; }
  .subhead { position: absolute; left: 45px; top: 246px; font-weight: 800; font-size: 22.5px; line-height: 25px; color: var(--yellow); }

  .badge { position: absolute; width: 140px; height: 140px; border-radius: 50%; display: flex; align-items: center; justify-content: center; text-align: center; }
  .badge--gold { left: 49px; top: 317px; background: radial-gradient(circle at 35% 30%, #fff3a6, var(--gold) 45%, var(--gold-dark) 100%); }
  .badge--bronze { left: 205px; top: 317px; background: radial-gradient(circle at 35% 30%, #ffe0a8, var(--bronze) 45%, #6e3f0e 100%); }
  .badge__core { width: 112px; height: 112px; border-radius: 50%; background: radial-gradient(circle at 40% 35%, #333, #0c0c0c); display: flex; flex-direction: column; align-items: center; justify-content: center; color: var(--white); }
  .badge__small { font-weight: 500; font-size: 7.5px; line-height: 10px; letter-spacing: 1.5px; }
  .badge__big { font-family: "Oswald", sans-serif; font-weight: 500; font-size: 11.5px; line-height: 13px; }
  .badge--bronze .badge__big { font-size: 19px; line-height: 20px; margin-top: 2px; }

  .book-back { position: absolute; left: 424px; top: 83px; width: 192px; height: 140px; background: linear-gradient(180deg, #f2ea2a, #ddd41e); }
  .book-yellow { position: absolute; left: 562px; top: 95px; width: 176px; height: 290px; transform: rotate(6deg); background: linear-gradient(135deg, #f7f03a, #d7cf18); }
  .book-open { position: absolute; left: 343px; top: 221px; width: 295px; height: 199px; background: linear-gradient(90deg, #e9e3d8, #f8f5ef 48%, #e6e0d4 52%, #f7f4ee); }

  .features { position: absolute; left: 48px; top: 518px; width: 682px; height: 257px; display: flex; }
  .feature { position: relative; flex: 1; padding: 48px 16px 0; text-align: center; color: var(--ink); }
  .feature:nth-child(odd) { background: var(--col-blue); }
  .feature:nth-child(even) { background: var(--col-yellow); }
  .feature:first-child { border-top-left-radius: 18px; }
  .feature:last-child { border-top-right-radius: 18px; }
  .feature__icon { position: absolute; left: 50%; top: -31px; margin-left: -31px; width: 62px; height: 62px; border-radius: 50%; background: var(--ink); border: 3px solid var(--yellow); box-shadow: 0 0 0 2px var(--white); display: flex; align-items: center; justify-content: center; }
  .feature__title { font-weight: 700; font-size: 14px; line-height: 16.5px; margin: 0 auto 5px; max-width: 118px; }
  .feature__text { font-weight: 400; font-size: 13.5px; line-height: 16.7px; }

  .contents { position: absolute; left: 0; top: 775px; width: 773px; height: 425px;
    background: radial-gradient(ellipse at 75% 55%, #2b2f8a 0%, #141a5a 35%, var(--navy-deep) 80%); }
  .book-cover { position: absolute; left: 46px; top: 49px; width: 290px; height: 308px; background: linear-gradient(135deg, #f5ee30, #d8d01a); }
  .contents__title { position: absolute; left: 364px; top: 40px; font-weight: 700; font-size: 16.5px; color: var(--white); }
  .contents__title em { font-style: normal; color: var(--yellow); }
  .chapter-list { position: absolute; left: 354px; top: 73px; width: 373px; list-style: none; }
  .chapter-list li { height: 32px; margin-bottom: 4.5px; border: 1.5px solid var(--yellow); border-radius: 16px; background: var(--navy); color: var(--white); font-size: 13px; font-weight: 400; line-height: 29px; padding-left: 13px; white-space: nowrap; }
</style>
</head>
<body>
<main class="poster">
  <div class="top-band"></div>
  <div class="hero-backdrop" role="img" aria-label="Photo of Earth from space with a glowing blue horizon"></div>

  <h1 class="headline">
    <span class="accent">Embark on a</span>
    <span class="main">Mind-Bending</span>
    <span class="main">Journey</span>
  </h1>
  <p class="subhead">INTO THE REALM OF<br>QUANTUM PHYSICS</p>

  <div class="book-back" role="img" aria-label="Back cover of the yellow book with description text"></div>
  <div class="book-yellow" role="img" aria-label="Yellow front cover of the book Quantum Horizons by Milo Fenwright"></div>
  <div class="book-open" role="img" aria-label="Open book showing the first chapter pages"></div>

  <div class="badge badge--gold">
    <div class="badge__core">
      <span class="badge__small">IDEAL FOR</span>
      <span class="badge__big">SCIENCE STUDENTS,<br>QUANTUM COMPUTING<br>ENTHUSIASTS</span>
    </div>
  </div>
  <div class="badge badge--bronze">
    <div class="badge__core">
      <span class="badge__small">PERFECT GIFT<br>FOR THE</span>
      <span class="badge__big">SCIENCE<br>LOVER</span>
    </div>
  </div>

  <section class="features">
    <article class="feature">
      <div class="feature__icon">
        <svg width="34" height="34" viewBox="0 0 34 34" fill="none" stroke="#fff" stroke-width="1.4">
          <ellipse cx="17" cy="17" rx="15" ry="6"/>
          <ellipse cx="17" cy="17" rx="15" ry="6" transform="rotate(60 17 17)"/>
          <ellipse cx="17" cy="17" rx="15" ry="6" transform="rotate(120 17 17)"/>
          <circle cx="17" cy="17" r="2.5" fill="#fff"/>
        </svg>
      </div>
      <h2 class="feature__title">History of quantum mechanics</h2>
      <p class="feature__text">Explore the fascinating history of quantum mechanics and the brilliant minds behind its development</p>
    </article>
    <article class="feature">
      <div class="feature__icon">
        <svg width="34" height="34" viewBox="0 0 34 34" fill="none" stroke="#fff" stroke-width="1.4">
          <path d="M6 20h22v6a3 3 0 0 1-3 3H9a3 3 0 0 1-3-3z"/>
          <path d="M10 17c-2-3 2-5 0-9M17 17c-2-3 2-5 0-9M24 17c-2-3 2-5 0-9"/>
          <path d="M8 7l2-2 2 2M15 7l2-2 2 2M22 7l2-2 2 2"/>
        </svg>
      </div>
      <h2 class="feature__title">Fundamental principles of wave&#8209;particle</h2>
      <p class="feature__text">Grasp the fundamental principles of wave&#8209;particle duality, quantum states, and the uncertainty principle</p>
    </article>
    <article class="feature">
      <div class="feature__icon">
        <svg width="34" height="34" viewBox="0 0 34 34" fill="none" stroke="#fff" stroke-width="1.4">
          <rect x="8" y="8" width="18" height="18" rx="2"/>
          <path d="M12 12l10 10M22 12L12 22"/>
          <circle cx="17" cy="17" r="3"/>
          <path d="M12 4v4M17 4v4M22 4v4M12 26v4M17 26v4M22 26v4M4 12h4M4 17h4M4 22h4M26 12h4M26 17h4M26 22h4"/>
        </svg>
      </div>
      <h2 class="feature__title">Quantum entanglement</h2>
      <p class="feature__text">Dive into the strange and counterintuitive world of quantum entanglement and its implications for reality itself</p>
    </article>
    <article class="feature">
      <div class="feature__icon">
        <svg width="34" height="34" viewBox="0 0 34 34" fill="none" stroke="#fff" stroke-width="1.4">
          <path d="M12 11V8a5 5 0 0 1 10 0v3"/>
          <rect x="10" y="11" width="14" height="11" rx="2"/>
          <path d="M17 22v8M10 16H4M24 16h6M12 22l-4 5M22 22l4 5"/>
          <circle cx="4" cy="16" r="1.5"/><circle cx="30" cy="16" r="1.5"/><circle cx="17" cy="30" r="1.5"/>
        </svg>
      </div>
      <h2 class="feature__title">Quantum computing to cryptography</h2>
      <p class="feature__text">Learn about the cutting&#8209;edge applications of quantum mechanics, from quantum computing to cryptography</p>
    </article>
  </section>

  <section class="contents">
    <div class="book-cover" role="img" aria-label="Yellow book cover of Quantum Horizons by Milo Fenwright, with its back cover behind"></div>
    <h2 class="contents__title"><em>In this book</em> you will find:</h2>
    <ul class="chapter-list">
      <li>The Quantum World Unveiled</li>
      <li>The Mathematical Symphony of Quantum Mechanics</li>
      <li>Beyond Classical Boundaries</li>
      <li>Quantum Mechanics at Work</li>
      <li>Bridging Quantum Mechanics and Relativity</li>
      <li>Quantum Paradoxes and Thought Experiments</li>
      <li>Quantum Mechanics for the Curious Mind</li>
      <li>Quantum Mechanics Demystified – A Practical Guide</li>
    </ul>
  </section>
</main>
</body>
</html>
```